graphic showing our process of education as a process called a pipeline

Also see my updated comments on discussion section.
Title of the graphic needs to be:
TITLE = The KESIMA Strategic Leadership Pipeline = larger, bold heading
SUB-TITLE = Developing a steady flow of servant leaders for Tanzania's future = under title; smaller font
change the text for each of the 7 steps to match the outcomes listed on the newly attached PDF (strategic pipeline 11x17)
Pipe should be straight or mostly straight.
Pipe should not be in a strong or dark color.
Any icons or symbols should be simple and professional, not like cartoon or childish.
We need a graphic design that shows our PROCESS, called a "pipeline," that is creating future leaders. We are a US-based non-profit that operates a Christian school in rural Tanzania for 600 students (pre-K through 12th grade). It starts with child sponsorship program that allows poor children and orphans to attend school, we have a primary school (like USA elementary school, pre-K thru 7th), and are building a secondary boarding school (like USA middle and high school, grades 8-12), where students will live on campus in dormitories. We offer education, scholarships, leadership development experiences, help finding and securing college scholarships, academic and career counseling, placements for internships and jobs, and networking and leadership development content and events to create the next generation of servant leaders for the country. Prominent colors should probably be the green, blue and black in the Tanzania flag; we want the design to communicate "smart" and "strategic." The stages of the pipeline need to be properly named; we need to show a "leak" in the pipeline after the primary school because we currently have to send our students AWAY to other boarding schools because we don't have one. As the attached recording says, this is bad for their progress. The attached pipeline graphic is very rough and NOT meant to be imitated. It is factually correct, but is busy and not attractive.

Target Market(s)

Major financial contributors and foundations that want to give money to the cause

Industry/Entity Type

non-profit/Christian ministry in education

Font styles to use
Sans Serif

Requirements
Must have
• A "smart" and strategic" feel; preferably visible when on a half page
Nice to have
• a smart, sophisticated, serious look and feel
Should not have
• an elementary school feel

```html
<!DOCTYPE html>
<html lang="en">
<head>
<meta charset="utf-8">
<title>KESIMA Leadership Pipeline</title>
<link href="https://fonts.googleapis.com/css2?family=Montserrat:wght@500;600;700&display=swap" rel="stylesheet">
<style>
  :root {
    --blue: #1a9bd7;
    --green: #2bb34a;
    --ink: #111111;
    --pipe: #dcdcdc;
    --paper: #ffffff;
  }
  * { margin: 0; padding: 0; box-sizing: border-box; }
  html, body { width: 1200px; height: 1200px; overflow: hidden; background: var(--paper); }
  .canvas {
    position: relative;
    width: 1200px;
    height: 1200px;
    font-family: 'Montserrat', Arial, sans-serif;
    color: var(--ink);
  }
  .title {
    position: absolute;
    top: 312px; left: 0; width: 1200px;
    text-align: center;
    font-size: 45px;
    font-weight: 700;
    color: var(--blue);
    letter-spacing: 0.2px;
  }
  .subtitle {
    position: absolute;
    top: 374px; left: 0; width: 1200px;
    text-align: center;
    font-size: 22.5px;
    font-weight: 500;
  }
  .rule {
    position: absolute;
    top: 389px;
    height: 1.5px;
    width: 70px;
    background: var(--green);
  }
  .rule--left { left: 174px; }
  .rule--right { left: 962px; }
  .stage-label {
    position: absolute;
    top: 429px;
    width: 112px;
    height: 64px;
    background: var(--blue);
    color: #fff;
    font-size: 11.5px;
    font-weight: 700;
    line-height: 13.5px;
    text-align: center;
    display: flex;
    align-items: center;
    justify-content: center;
  }
  .stage-icon {
    position: absolute;
    top: 503px;
    width: 56px;
    height: 56px;
    border-radius: 6px;
    background: var(--green);
  }
  .outcome {
    position: absolute;
    top: 690px;
    width: 130px;
    text-align: center;
  }
  .outcome-heading {
    font-size: 12.5px;
    font-weight: 500;
    color: var(--blue);
    margin-bottom: 1px;
  }
  .outcome-text {
    font-size: 9.6px;
    font-weight: 600;
    line-height: 11px;
  }
  .pipeline { position: absolute; top: 0; left: 0; }
</style>
</head>
<body>
<div class="canvas">
  <h1 class="title">KESIMA Leadership Pipeline</h1>
  <span class="rule rule--left"></span>
  <p class="subtitle">Developing a steady flow of servant leaders for Tanzania</p>
  <span class="rule rule--right"></span>

  <div class="stage-label" style="left:129px">SPONSORSHIP<br>PROGRAM</div>
  <div class="stage-label" style="left:268px">PRIMARY<br>SCHOOL</div>
  <div class="stage-label" style="left:407px">SECONDARY<br>SCHOOL</div>
  <div class="stage-label" style="left:546px">SERVICE<br>LEADERSHIP<br>EXPERIENCE</div>
  <div class="stage-label" style="left:685px">HIGHER<br>EDUCATION<br>SUPPORT</div>
  <div class="stage-label" style="left:824px">EMPLOYMENT<br>CENTER</div>
  <div class="stage-label" style="left:963px">LEADERSHIP<br>HUB</div>

  <div class="stage-icon" style="left:157px" role="img" aria-label="Icon of an adult caring for a child"></div>
  <div class="stage-icon" style="left:296px" role="img" aria-label="Icon of a young pupil with raised arms"></div>
  <div class="stage-icon" style="left:435px" role="img" aria-label="Icon of a student beside an atom symbol"></div>
  <div class="stage-icon" style="left:575px" role="img" aria-label="Icon of a person helping another person up"></div>
  <div class="stage-icon" style="left:713px" role="img" aria-label="Icon of a graduate holding a diploma"></div>
  <div class="stage-icon" style="left:852px" role="img" aria-label="Icon of a professional walking with a briefcase"></div>
  <div class="stage-icon" style="left:991px" role="img" aria-label="Icon of a large group of people"></div>

  <svg class="pipeline" width="1200" height="1200" viewBox="0 0 1200 1200" aria-hidden="true">
    <g stroke="#1a9bd7" stroke-width="2.2" stroke-dasharray="2 3.2" stroke-linecap="round" fill="none">
      <path d="M184 568 V634 L218 652"/>
      <line x1="323" y1="568" x2="323" y2="630"/>
      <line x1="462" y1="568" x2="462" y2="630"/>
      <line x1="603" y1="568" x2="603" y2="630"/>
      <line x1="741" y1="568" x2="741" y2="630"/>
      <line x1="880" y1="568" x2="880" y2="630"/>
      <line x1="1019" y1="568" x2="1019" y2="630"/>
    </g>
    <polygon points="228,647 218,660 229,659" fill="#1a9bd7"/>
    <rect x="247" y="642" width="857" height="28" fill="var(--pipe)"/>
    <g fill="#1a9bd7">
      <rect x="241" y="637" width="3.5" height="38"/><rect x="247" y="637" width="3.5" height="38"/>
      <rect x="523" y="637" width="3.5" height="38"/><rect x="529" y="637" width="3.5" height="38"/>
      <rect x="805" y="637" width="3.5" height="38"/><rect x="811" y="637" width="3.5" height="38"/>
      <rect x="1095" y="637" width="3.5" height="38"/><rect x="1101" y="637" width="3.5" height="38"/>
      <polygon points="388,642 395,642 392,651 402,651 391,667 394,656 386,656"/>
    </g>
    <g stroke="#1a9bd7" stroke-width="1.6" fill="none">
      <path d="M389 676 C385 683 380 687 382 692 C384 697 392 696 392 690"/>
    </g>
    <path d="M396 681 C392 690 388 694 390 700 C392 706 402 706 404 700 C406 694 400 690 396 681 Z" fill="#1a9bd7"/>
  </svg>

  <div class="outcome" style="left:117px">
    <div class="outcome-heading">OUTCOME</div>
    <div class="outcome-text">Children strengthened<br>spiritually, academically,<br>and nutritionally</div>
  </div>
  <div class="outcome" style="left:256px">
    <div class="outcome-heading">OUTCOME</div>
    <div class="outcome-text">Potential leaders<br>with Biblical<br>worldview and<br>strong academic<br>foundations.</div>
  </div>
  <div class="outcome" style="left:397px">
    <div class="outcome-heading">OUTCOME</div>
    <div class="outcome-text">Emerging leaders<br>with concrete<br>skills and<br>strong servant<br>mindset.</div>
  </div>
  <div class="outcome" style="left:538px">
    <div class="outcome-heading">OUTCOME</div>
    <div class="outcome-text">Growing servant<br>leaders with<br>practical<br>experience<br>to effect change<br>for the kingdom</div>
  </div>
  <div class="outcome" style="left:676px">
    <div class="outcome-heading">OUTCOME</div>
    <div class="outcome-text">Visionary leaders<br>with expanded<br>capability to solve<br>Tanzania's<br>biggest challenges</div>
  </div>
  <div class="outcome" style="left:809px">
    <div class="outcome-heading">OUTCOME</div>
    <div class="outcome-text">Capable<br>Christ-centered<br>leaders in the<br>marketplace as<br>value adding<br>employees and<br>entrepreneurs.</div>
  </div>
  <div class="outcome" style="left:949px; top:691px">
    <div class="outcome-heading">OUTCOME</div>
    <div class="outcome-text">Mature Christian<br>leaders being<br>placed and<br>positioned for<br>leadership roles<br>in the community<br>and nation.</div>
  </div>
</div>
</body>
</html>
```